Baby Boutique Needs a Business Card Design

We need a modern double sided business card design using the attached logo for Little Wren Nook.

Little Wren Nook is a baby boutique which sells only handmade clothing and accessories for both boys and girls. Our store will live exclusively online.

We would like to only use the colors that have been used in the logo.

Target Market(s)

Potential wholesale clients, Small business owners

Industry/Entity Type

Retail

Contact Information for Business Card

Name Gideon R. Falkner (Owner)
Email sales@littlewrennook.example
Main Phone 555-203-7719
Cell phone 555-203-7746
Website www.LittleWrenNook.example

Font styles to use
Sans Serif

Colors

Designer to choose colors to be used in the design.

Requirements
Must have
• -Would like to have icons that indentify the contact information.
• -Include our website
• -Include our tagline in a small area near the bottom. "Handmade Baby Creations"
• -Would like to include Facebook and Instagram Icons
• -
Nice to have
• Would like to have a simple back side with the logo.
• Something along the lines of the meadowfield lending card attached.

```html
<!DOCTYPE html>
<html lang="en">
<head>
<meta charset="utf-8">
<title>Little Wren Nook — Business Card</title>
<link rel="stylesheet" href="https://fonts.googleapis.com/css2?family=Work+Sans:wght@400;500;600&display=swap">
<style>
  :root {
    --stage: #2b2b2c;
    --card: #1b1b1c;
    --teal: #6fd3c0;
    --coral: #e8625f;
    --ink-light: #f1f1f1;
  }
  * { box-sizing: border-box; margin: 0; padding: 0; }
  html, body {
    width: 1200px; height: 900px; overflow: hidden;
    background: var(--stage);
    font-family: "Work Sans", sans-serif;
  }
  .stage {
    position: relative; width: 1200px; height: 900px;
    display: flex; flex-direction: column; align-items: center; justify-content: center; gap: 48px;
  }
  .card {
    position: relative; width: 620px; height: 354px;
    background: var(--card);
    border-radius: 4px;
    box-shadow: 0 14px 30px rgba(0,0,0,0.45);
  }
  .brand-name {
    color: var(--teal);
    font-weight: 600;
    line-height: 1.02;
    letter-spacing: 0.01em;
  }
  /* back side */
  .card-back { display: flex; align-items: center; justify-content: center; }
  .card-back .brand-name { font-size: 46px; text-align: center; }

  /* front side */
  .card-front .brand {
    position: absolute; left: 48px; top: 112px; width: 190px;
  }
  .card-front .brand-name { font-size: 34px; }
  .divider {
    position: absolute; left: 262px; top: 92px;
    width: 2px; height: 160px; background: var(--teal);
  }
  .contact {
    position: absolute; left: 292px; top: 98px;
  }
  .person-name { color: var(--coral); font-size: 25px; font-weight: 500; letter-spacing: 0.02em; }
  .person-role { color: var(--teal); font-size: 15px; margin-top: 0; letter-spacing: 0.03em; }
  .contact-list { list-style: none; margin-top: 18px; }
  .contact-item {
    display: flex; align-items: center; gap: 10px;
    color: var(--teal); font-size: 15.5px; letter-spacing: 0.04em; line-height: 23px;
  }
  .contact-item svg { width: 12px; height: 12px; flex: none; }
  .contact-item .accent { color: var(--coral); }
  .tagline {
    position: absolute; left: 160px; bottom: 50px;
    color: var(--ink-light); font-size: 16px; letter-spacing: 0.06em;
  }
  .social {
    position: absolute; right: 72px; bottom: 42px; display: flex; gap: 16px;
  }
  .social-mark { width: 24px; height: 24px; border-radius: 4px; background: var(--coral); }
</style>
</head>
<body>
<main class="stage">
  <section class="card card-back" aria-label="Card back">
    <div class="brand-name">Little Wren<br>Nook</div>
  </section>

  <section class="card card-front" aria-label="Card front">
    <div class="brand"><div class="brand-name">Little Wren<br>Nook</div></div>
    <div class="divider"></div>
    <div class="contact">
      <div class="person-name">Gideon R. Falkner</div>
      <div class="person-role">Owner</div>
      <ul class="contact-list">
        <li class="contact-item">
          <svg viewBox="0 0 12 12" aria-hidden="true"><path d="M2.5 1h2l1 3-1.3 1a6 6 0 0 0 2.8 2.8L8 6.5l3 1v2A1.5 1.5 0 0 1 9.5 11 8.5 8.5 0 0 1 1 2.5 1.5 1.5 0 0 1 2.5 1z" fill="none" stroke="#e8625f" stroke-width="1.2"/></svg>
          555-203-7719
        </li>
        <li class="contact-item">
          <svg viewBox="0 0 12 12" aria-hidden="true"><rect x="3" y="0.8" width="6" height="10.4" rx="1" fill="none" stroke="#e8625f" stroke-width="1.2"/><circle cx="6" cy="9.2" r="0.7" fill="#e8625f"/></svg>
          555-203-7746
        </li>
        <li class="contact-item">
          <svg viewBox="0 0 12 12" aria-hidden="true"><rect x="0.8" y="2.5" width="10.4" height="7" rx="0.8" fill="none" stroke="#e8625f" stroke-width="1.2"/><path d="M1 3l5 3.5L11 3" fill="none" stroke="#e8625f" stroke-width="1.2"/></svg>
          sales@littlewrennook.example
        </li>
        <li class="contact-item">
          <svg viewBox="0 0 12 12" aria-hidden="true"><circle cx="6" cy="6" r="5" fill="none" stroke="#e8625f" stroke-width="1.1"/><ellipse cx="6" cy="6" rx="2.2" ry="5" fill="none" stroke="#e8625f" stroke-width="1"/><path d="M1 6h10" stroke="#e8625f" stroke-width="1"/></svg>
          <span>www.<span class="accent">LittleWrenNook</span>.example</span>
        </li>
      </ul>
    </div>
    <p class="tagline">Handmade Baby Creations</p>
    <div class="social">
      <span class="social-mark" role="img" aria-label="Social profile icon"></span>
      <span class="social-mark" role="img" aria-label="Social profile icon"></span>
    </div>
  </section>
</main>
</body>
</html>
```